Recruitment of Tavira Workforce for the UK market

I want a website for the UK market to attract businesses and companies to come to us for Philipine labour. We want an information site that gives all information on what we do and how we can recruit Philippine labour.
This is a recruitment site for companies to contact us with their requirements for skilled workers coming from the Philipines over to the UK to work.

Target Market(s)

Uk Companies and businesses who want Philipine skilled workers

Industry/Entity Type

REcruitment

Coding

Number of Pages Required

5+ page

Font styles to use
Sans Serif

Colors
0054AA
0677BA
7BADD7
CADEEF
E8F1F8
0094D4
00A9DD
6FCCEA
C7EBF8
E9F6FB
EE7325
F08F49
F5BC92
FAE3D3
FDF4ED
EB3D1F
EC4F4E
F09395
F8D3D4
FCEDEE

Requirements
Must have
• Look professional and corperate with drop down menus for Home ,about, services,articles. training , contact us
Nice to have
• Look at Velmora recruitment- https://velmorarecruitment.example.co.uk/. This is my current site - https://www.trellanstaffing.example.com/
Should not have
• Cartoons or silly pictures , needs to be corperate looking

```html
<!DOCTYPE html>
<html lang="en">
<head>
<meta charset="utf-8">
<title>Tavira Workforce – Skilled Philippine workers for UK companies</title>
<link href="https://fonts.googleapis.com/css2?family=Raleway:wght@400;500;600&family=Roboto:wght@400;500;700&display=swap" rel="stylesheet">
<style>
:root{
  --red:#e8401f;
  --red-deep:#c0311a;
  --red-dark:#8c2c24;
  --card-1:#cf6159;
  --card-2:#a8453c;
  --card-3:#8e3a31;
  --ink:#1d1d1d;
  --body:#444;
  --mist:#eef3f6;
  --panel:#f6f3f2;
  --white:#fff;
  --line:#d8d8d8;
}
*{box-sizing:border-box;margin:0;padding:0}
html,body{width:1200px;height:4930px;overflow:hidden}
body{position:relative;background:var(--white);font-family:"Roboto",Arial,sans-serif;color:var(--body)}
.abs{position:absolute}
h1,h2,h3{font-family:"Raleway",Arial,sans-serif;font-weight:500;color:var(--ink)}
p{font-size:13px;line-height:22px}
.btn{position:absolute;display:flex;align-items:center;justify-content:center;border-radius:20px;font-size:11px;font-weight:500;text-transform:uppercase;letter-spacing:.3px}
.hex{clip-path:polygon(25% 0,75% 0,100% 50%,75% 100%,25% 100%,0 50%)}

/* hero */
.hero{left:34px;top:0;width:1166px;height:650px;background:var(--red);border-bottom-left-radius:90px}
.brand{display:flex;align-items:center;gap:10px;color:var(--white);font-family:"Raleway",Arial,sans-serif;font-weight:600;font-size:22px}
.brand-mark{width:26px;height:26px;border-radius:50%;background:var(--white)}
.nav{left:590px;top:22px;display:flex;gap:30px;list-style:none}
.nav li{color:var(--white);font-size:12px;text-transform:uppercase}
.hero-kicker{left:107px;top:226px;color:var(--white);font-family:"Raleway",sans-serif;font-size:24px}
.hero-title{left:107px;top:258px;color:var(--white);font-size:42px;line-height:54px}
.hero-btn{left:107px;top:392px;width:146px;height:37px;background:var(--white);color:var(--ink)}
.hero-photo{left:650px;top:76px;width:550px;height:574px;background:linear-gradient(160deg,#f2f2f2 0%,#d9d9d9 45%,#2d3a4f 100%);opacity:.95}
.contact-bar{left:0;top:545px;width:628px;height:67px;background:var(--red-deep);border-radius:0 34px 34px 0;display:flex;align-items:center;gap:36px;padding-left:106px;color:var(--white);font-size:13px}
.contact-bar span{display:flex;align-items:center;gap:10px}
.icon-dot{width:30px;height:30px;border-radius:50%;background:rgba(0,0,0,.18);display:flex;align-items:center;justify-content:center}

/* about */
.kicker{font-size:13px;color:var(--ink)}
.title-lg{font-size:42px;line-height:52px}
.btn-red{background:var(--red);color:var(--white)}

/* sectors */
.sectors{left:107px;top:1386px;width:986px;height:470px;display:grid;grid-template-columns:repeat(4,1fr);grid-template-rows:repeat(2,1fr)}
.sector{padding:58px 22px 0}
.sector h3{font-size:18px;margin-bottom:14px}
.sector p{font-size:10.5px;line-height:20px}
.sector--shade{background:var(--panel)}
.photo{width:100%;height:100%}

/* working together */
.center{text-align:center;left:0;width:1200px}
.feature h3{font-size:22px;margin-bottom:22px}
.feature p{width:490px}

/* training */
.train-card{padding:0 22px;color:var(--white)}
.train-card h3{color:var(--white);font-size:17px;margin:10px 0 10px}
.train-card p{font-size:10.5px;line-height:19px;color:rgba(255,255,255,.85)}
.nc-list{list-style:none;font-size:11px;line-height:32px;color:var(--ink)}
.nc-list li::before{content:"";display:inline-block;width:5px;height:5px;background:var(--red);border-radius:50%;margin-right:6px;vertical-align:middle}

/* get in touch */
.touch-item{display:flex;gap:14px;font-size:12px;color:var(--ink);align-items:flex-start}
.form-card{left:714px;top:4176px;width:379px;height:400px;background:var(--white);box-shadow:0 4px 24px rgba(0,0,0,.12);z-index:2}
.field{position:absolute;left:44px;width:293px;border:1px solid #cfcfcf;font-size:10px;color:#666;padding:10px 8px}

/* footer */
.footer{left:0;top:4540px;width:1200px;height:390px;background:var(--red)}
.footer p{color:var(--white);font-size:11.5px;line-height:20px}
.foot-nav{display:flex;gap:64px;list-style:none;color:var(--white);font-size:11.5px;text-transform:uppercase}
.social{display:flex;gap:19px}
.social span{width:32px;height:32px;border-radius:50%;background:rgba(0,0,0,.2)}
</style>
</head>
<body>

<!-- hero -->
<div class="abs hero"></div>
<div class="abs hero-photo" role="img" aria-label="Two business professionals, one holding a tablet"></div>
<div class="abs brand" style="left:107px;top:18px"><span class="brand-mark"></span>Tavira Workforce</div>
<ul class="abs nav"><li>Home</li><li>About</li><li>Services</li><li>Articles</li><li>Training</li><li>Contact us</li></ul>
<div class="abs hero-kicker">Recruiting and placing</div>
<h1 class="abs hero-title">Skilled Philippine workers<br>into UK Companies</h1>
<div class="btn hero-btn">Explore more</div>
<div class="abs contact-bar">
  <span><i class="icon-dot"><svg width="14" height="14" viewBox="0 0 24 24"><path fill="#fff" d="M6.6 10.8a15 15 0 0 0 6.6 6.6l2.2-2.2a1 1 0 0 1 1-.25 11.4 11.4 0 0 0 3.6.57 1 1 0 0 1 1 1V20a1 1 0 0 1-1 1A17 17 0 0 1 3 4a1 1 0 0 1 1-1h3.5a1 1 0 0 1 1 1 11.4 11.4 0 0 0 .57 3.6 1 1 0 0 1-.25 1z"/></svg></i>Call: 07700 900412</span>
  <span><i class="icon-dot"><svg width="14" height="14" viewBox="0 0 24 24"><path fill="#fff" d="M3 5h18v14H3zm2 2v.5l7 4.5 7-4.5V7l-7 4.5z"/></svg></i>Email: sales@taviraworkforce.example.com</span>
</div>

<!-- about -->
<svg class="abs" style="left:0;top:727px" width="560" height="420" viewBox="0 0 560 420">
  <polyline points="0,103 100,103 160,3 435,3" fill="none" stroke="#333" stroke-width="1"/>
  <polyline points="0,316 100,316 160,416 435,416" fill="none" stroke="#333" stroke-width="1"/>
  <defs>
    <linearGradient id="gA" x1="0" y1="0" x2="1" y2="1"><stop offset="0" stop-color="#8aa3bd"/><stop offset="1" stop-color="#e88b3a"/></linearGradient>
    <linearGradient id="gB" x1="0" y1="0" x2="1" y2="1"><stop offset="0" stop-color="#e9e9e9"/><stop offset="1" stop-color="#c23a2a"/></linearGradient>
    <linearGradient id="gC" x1="0" y1="0" x2="1" y2="1"><stop offset="0" stop-color="#9aa3ac"/><stop offset="1" stop-color="#2d3440"/></linearGradient>
  </defs>
  <g role="img" aria-label="Construction workers and engineers on site">
    <polygon points="185,43 330,43 265,230 124,230" fill="url(#gA)"/>
    <polygon points="390,43 545,230 445,372 335,235" fill="url(#gB)"/>
    <polygon points="135,245 325,245 425,372 195,372" fill="url(#gC)"/>
  </g>
</svg>
<div class="abs kicker" style="left:655px;top:804px">What The</div>
<h2 class="abs title-lg" style="left:655px;top:820px">Business is About</h2>
<p class="abs" style="left:655px;top:892px;width:440px">We source skilled workers directly from the Philippines to work in the UK. With offices , training locations and specialist recruiters we can find the highest quality individuals to add value and resources to any UK buisness. We delivery quality based on vast experience over a number of years.</p>
<div class="btn btn-red" style="left:655px;top:1028px;width:145px;height:36px">Read more</div>

<!-- sectors -->
<h2 class="abs title-lg" style="left:107px;top:1220px">We help you find the<br>Right people for your Business</h2>
<div class="abs sectors">
  <div class="photo" role="img" aria-label="Hands holding soil with a young seedling" style="background:linear-gradient(135deg,#5e6b5a,#1e1f1d)"></div>
  <div class="sector sector--shade"><h3>Agriculture</h3><p>Sed ut perspiciatis unde omnis iste natus error sit voluptatem accusantium doloremque laudantium, totam rem aperiam</p></div>
  <div class="sector"><h3>Building &amp; Construction</h3><p>Sed ut perspiciatis unde omnis iste natus error sit voluptatem accusantium doloremque laudantium, totam rem aperiam</p></div>
  <div class="photo" role="img" aria-label="Engineer with plans in front of a high-rise" style="background:linear-gradient(160deg,#dfe6ee,#6f7c8a)"></div>
  <div class="photo" role="img" aria-label="Waiting staff serving diners in a restaurant" style="background:linear-gradient(135deg,#e9e2d6,#5b4a3e)"></div>
  <div class="sector"><h3>Hospitality &amp; Catering</h3><p>Sed ut perspiciatis unde omnis iste natus error sit voluptatem accusantium doloremque laudantium, totam rem aperiam</p></div>
  <div class="photo" role="img" aria-label="Logistics worker in a hi-vis vest beside lorries" style="background:linear-gradient(135deg,#3a5fa8,#b7c94a)"></div>
  <div class="sector"><h3>Transport &amp; Logistic</h3><p>Sed ut perspiciatis unde omnis iste natus error sit voluptatem accusantium doloremque laudantium, totam rem aperiam</p></div>
</div>

<!-- working together -->
<h2 class="abs center" style="top:1938px;font-size:40px">Working Together</h2>
<div class="abs center" style="top:2000px;font-size:12px;color:var(--ink)">We recruit the finest talent available with our dedicated 200 strong team. Our centres are highlighted in red dots on the map.</div>

<svg class="abs" style="left:122px;top:2064px" width="400" height="326"><polygon points="98,1 302,1 399,163 302,325 98,325 1,163" fill="none" stroke="#d8d8d8"/></svg>
<div class="abs hex" style="left:128px;top:2071px;width:385px;height:312px;background:linear-gradient(135deg,#3c8dc6,#b88a5a)" role="img" aria-label="Business people fitting jigsaw pieces together"></div>
<div class="abs feature" style="left:599px;top:2145px"><h3>What We Do</h3><p>Our company has been estabilished in the Philippines for over 20 years. We have mainly been recruiting philippine workers for the off shore industry in asia but since brexit and the new rules on skilled workers entering the UK we have been working with UK companies who now have chance to recruit some of the finest hard working talent from the Philippines for their companies..</p></div>

<svg class="abs" style="left:679px;top:2382px" width="394" height="337"><polygon points="97,1 297,1 393,168 297,336 97,336 1,168" fill="none" stroke="#d8d8d8"/></svg>
<div class="abs hex" style="left:685px;top:2389px;width:381px;height:323px;background:linear-gradient(135deg,#6b5a4a,#d9925a)" role="img" aria-label="Hand holding a ring of wooden figures"></div>
<div class="abs feature" style="left:107px;top:2468px"><h3>How we Help</h3><p>Our company has been estabilished in the Philippines for over 20 years. We have mainly been recruiting philippine workers for the off shore industry in asia but since brexit and the new rules on skilled workers entering the UK we have been working with UK companies who now have chance to recruit some of the finest hard working talent from the Philippines for their companies..</p></div>

<svg class="abs" style="left:122px;top:2717px" width="400" height="334"><polygon points="98,1 302,1 399,167 302,333 98,333 1,167" fill="none" stroke="#d8d8d8"/></svg>
<div class="abs hex" style="left:128px;top:2724px;width:385px;height:319px;background:linear-gradient(180deg,#8fb7dc,#eef3f7)" role="img" aria-label="Road curving up into the sky with a traveller"></div>
<div class="abs feature" style="left:599px;top:2804px"><h3>Where to start</h3><p>We need to know what your issues are and how we can understand the personnal you require , over what time frame and the number of employees you need. Once this is estabilished we start sourcing workers in the Philippines that meet your criteria while starting the process in the UK to be able to have all the documents in place to deliver your company hard working skilled individuals.</p></div>

<svg class="abs" style="left:440px;top:3040px" width="640" height="330"><polyline points="0,328 540,328 638,165 540,2" fill="none" stroke="#d8d8d8"/></svg>
<div class="abs hex" style="left:685px;top:3047px;width:381px;height:316px;background:linear-gradient(135deg,#1f2a38,#8a96a3)" role="img" aria-label="Contact us sign beside a telephone"></div>
<div class="abs feature" style="left:107px;top:3126px"><h3>Contact us Today</h3><p>Please contact us today with your requirements , this can be care workers ,chef, welders, pipe fitters, caravan cabinet makers, medical workers. The UK list of required skills is extensive and the Philippines offersenglish speaking highly qualified hard working employees. Contact us today and make that first step to a highly motivated , quality skilled workforce.</p></div>

<!-- training -->
<div class="abs" style="left:0;top:3780px;width:513px;height:310px;background:var(--mist)"></div>
<div class="abs" style="left:1148px;top:3594px;width:52px;height:62px;background:var(--mist)"></div>
<div class="abs" style="left:846px;top:3803px;width:62px;height:62px;background:var(--mist)"></div>
<div class="abs" style="left:599px;top:3947px;width:62px;height:62px;background:var(--mist)"></div>
<div class="abs" style="left:997px;top:3967px;width:62px;height:62px;background:var(--mist)"></div>
<div class="abs kicker" style="left:107px;top:3476px">Corporate</div>
<h2 class="abs title-lg" style="left:107px;top:3492px">Employee Training</h2>
<p class="abs" style="left:107px;top:3568px;width:470px;font-size:12px">Sed ut perspiciatis unde omnis iste natus error sit voluptatem accusantium doloremque laudantium, totam rem aperiam, eaque ipsa quae ab illo inventore veritatis et quasi architecto beatae vitae dicta sunt explicabo.</p>
<div class="btn" style="left:107px;top:3667px;width:144px;height:35px;background:var(--red-dark);color:var(--white)">View all training</div>

<h3 class="abs" style="left:107px;top:3828px;font-size:19px;line-height:26px;font-weight:600">NC (National Certificate)<br>III NSKA:</h3>
<ul class="abs nc-list" style="left:107px;top:3894px"><li>Basic competencies</li><li>Common competencies</li><li>Core competencies</li></ul>

<div class="abs train-card" style="left:846px;top:3547px;width:247px;height:256px;background:var(--card-1);padding-top:30px">
  <svg width="64" height="64" viewBox="0 0 64 64" fill="none" stroke="#fff" stroke-width="2"><path d="M44 6l14 14-22 22-8-8z"/><path d="M30 36L10 56l-4-4 20-20"/><circle cx="46" cy="18" r="2"/></svg>
  <h3>Butchers</h3><p>Sed ut perspiciatis unde omnis iste natus error sit voluptatem accusantium doloremque laudantium totam rem aperiam</p>
</div>
<div class="abs train-card" style="left:599px;top:3690px;width:247px;height:257px;background:var(--card-2);padding-top:30px">
  <svg width="60" height="60" viewBox="0 0 64 64" fill="none" stroke="#fff" stroke-width="2"><path d="M16 28a10 10 0 0 1 6-18 12 12 0 0 1 20 0 10 10 0 0 1 6 18z"/><path d="M18 28v8h28v-8"/><circle cx="32" cy="46" r="10"/></svg>
  <h3>Cooks</h3><p>Sed ut perspiciatis unde omnis iste natus error sit voluptatem accusantium doloremque laudantium totam rem aperiam</p>
</div>
<div class="abs train-card" style="left:354px;top:3832px;width:245px;height:258px;background:var(--card-3);padding-top:30px">
  <svg width="64" height="64" viewBox="0 0 64 64" fill="none" stroke="#fff" stroke-width="2"><rect x="8" y="8" width="48" height="48" rx="3"/><rect x="18" y="22" width="28" height="24"/><path d="M8 16h48M16 12h4M26 12h4"/></svg>
  <h3>Bakers</h3><p>Sed ut perspiciatis unde omnis iste natus error sit voluptatem accusantium doloremque laudantium totam rem aperiam</p>
</div>

<!-- get in touch -->
<h2 class="abs title-lg" style="left:107px;top:4168px">Get In Touch</h2>
<p class="abs" style="left:107px;top:4234px;width:400px;font-size:11.5px;line-height:20px">Sed ut perspiciatis unde omnis iste natus error sit voluptatem accusantium doloremque laudantium, totam rem aperiam, eaque ipsa quae ab illo inventore veritatis</p>
<div class="abs touch-item" style="left:107px;top:4328px"><svg width="12" height="12" viewBox="0 0 24 24"><path fill="#e8401f" d="M6.6 10.8a15 15 0 0 0 6.6 6.6l2.2-2.2a1 1 0 0 1 1-.25 11.4 11.4 0 0 0 3.6.57 1 1 0 0 1 1 1V20a1 1 0 0 1-1 1A17 17 0 0 1 3 4a1 1 0 0 1 1-1h3.5a1 1 0 0 1 1 1 11.4 11.4 0 0 0 .57 3.6 1 1 0 0 1-.25 1z"/></svg>07700 900412</div>
<div class="abs touch-item" style="left:107px;top:4366px"><svg width="12" height="12" viewBox="0 0 24 24"><path fill="#e8401f" d="M3 5h18v14H3zm2 2v.5l7 4.5 7-4.5V7l-7 4.5z"/></svg>sales@taviraworkforce.example.com</div>
<div class="abs touch-item" style="left:107px;top:4405px;line-height:19px"><svg width="12" height="14" viewBox="0 0 24 28"><path fill="#e8401f" d="M12 0a10 10 0 0 1 10 10c0 7-10 18-10 18S2 17 2 10A10 10 0 0 1 12 0zm0 6a4 4 0 1 0 0 8 4 4 0 0 0 0-8z"/></svg><span>Larkfield Gardens, Marbury MB18 1<br>United Kingdom</span></div>

<div class="abs form-card">
  <div class="abs" style="left:44px;top:36px;font-size:15px;font-weight:700;color:var(--ink)">SAY SOMETHING</div>
  <div class="field" style="top:67px;height:39px">Name</div>
  <div class="field" style="top:117px;height:39px">Email</div>
  <div class="field" style="top:169px;height:38px">Phone</div>
  <div class="field" style="top:218px;height:94px">Comments</div>
  <div class="abs" style="left:44px;top:324px;width:293px;height:38px;background:var(--red);color:var(--white);font-size:10px;font-weight:700;display:flex;align-items:center;justify-content:center">SEND</div>
</div>

<!-- footer -->
<footer class="abs footer">
  <div class="abs brand" style="left:107px;top:78px"><span class="brand-mark"></span>Tavira Workforce</div>
  <p class="abs" style="left:107px;top:140px;width:385px">We source skilled workers directly from the Philippines to work in the UK. With offices , training locations and specialist recruiters we can find the highest quality individuals to add value and resources to any UK buisness. We delivery quality based on vast experience over a number of years.</p>
  <p class="abs" style="left:905px;top:124px;font-size:10px;line-height:19px">Copyright © 2023<br>Tavira Workforce. All rights reserved.</p>
  <ul class="abs foot-nav" style="left:107px;top:296px"><li>Home</li><li>About us</li><li>Services</li><li>Training</li><li>Blog</li><li>Contact us</li></ul>
  <div class="abs social" style="left:907px;top:289px"><span></span><span></span><span></span><span></span></div>
</footer>

</body>
</html>
```